Kinesiology undergraduate program needs an infographic

We would like an infographic to creatively and succinctly inform students, faculty, staff, and others about our undergraduate values and competencies (perhaps also integrating our mission and vision). We would like to see a design that incorporates the definition of Kinesiology (the study of human movement) and the colors of our Westbrook State University at Harlan.

```html
<!DOCTYPE html>
<html lang="en">
<head>
<meta charset="utf-8">
<title>Kinesiology Undergraduate Program</title>
<link href="https://fonts.googleapis.com/css2?family=Arimo:wght@400;500&display=swap" rel="stylesheet">
<style>
  :root {
    --navy: #14284b;
    --orange: #e84b26;
    --green: #5a8430;
    --grey-text: #7a7a7a;
    --bg-light: #ffffff;
    --bg-edge: #e1e6eb;
  }
  * { margin: 0; padding: 0; box-sizing: border-box; }
  html, body { width: 985px; height: 1200px; overflow: hidden; }
  body {
    font-family: "Arimo", Arial, sans-serif;
    color: var(--navy);
    background: radial-gradient(ellipse 620px 480px at 490px 230px, var(--bg-light) 0%, var(--bg-light) 35%, var(--bg-edge) 100%);
    position: relative;
  }
  .program-title {
    position: absolute; top: 92px; left: 0; width: 985px;
    text-align: center; font-weight: 400; font-size: 28px; line-height: 48px;
    letter-spacing: 0.3px;
  }
  .pillar { position: absolute; top: 275px; width: 250px; text-align: center; }
  .pillar-badge {
    position: relative; width: 168px; height: 44px; margin: 0 auto;
  }
  .pillar-badge .fill {
    position: absolute; left: 0; top: 3px; width: 165px; height: 41px;
    border-radius: 22px; color: #fff; font-size: 28px; line-height: 41px;
    text-align: center;
  }
  .pillar-badge::after {
    content: ""; position: absolute; left: 3px; top: 0; width: 165px; height: 41px;
    border: 1.2px solid var(--navy); border-radius: 22px;
  }
  .mission .fill { background: var(--orange); }
  .vision .fill { background: var(--navy); }
  .values .fill { background: var(--green); }
  .pillar-text {
    margin-top: 40px; font-size: 11.5px; line-height: 15px; color: var(--grey-text);
  }
  .mission { left: 71px; }
  .vision { left: 355px; }
  .values { left: 654px; }
  .values .pillar-text { width: 260px; margin-left: -5px; }

  .competency-heading {
    position: absolute; top: 517px; left: 0; width: 985px; text-align: center;
    font-size: 35px; font-weight: 500; letter-spacing: 0.2px;
  }
  .domain { position: absolute; }
  .domain-label {
    display: block; height: 42px; border: 1.2px solid var(--navy); border-radius: 21px;
    font-size: 20px; line-height: 40px; text-align: center; letter-spacing: 0.2px;
  }
  .domain-list { list-style: none; position: absolute; top: 85px; }
  .domain-list li { font-size: 16px; line-height: 30px; white-space: nowrap; }
  .science { left: 90px; top: 643px; }
  .science .domain-label { width: 350px; }
  .science .domain-list { left: 19px; }
  .thinking { left: 567px; top: 643px; }
  .thinking .domain-label { width: 305px; }
  .thinking .domain-list { left: 19px; }
  .relationships { left: 60px; top: 884px; }
  .relationships .domain-label { width: 410px; }
  .relationships .domain-list { left: 49px; }
  .growth { left: 567px; top: 884px; }
  .growth .domain-label { width: 305px; }
  .growth .domain-list { left: 19px; }
</style>
</head>
<body>
  <h1 class="program-title">KINESIOLOGY UNDERGRADUATE<br>PROGRAM</h1>

  <section class="pillar mission">
    <div class="pillar-badge"><span class="fill">MISSION</span></div>
    <p class="pillar-text">To empower undergraduate students to pursue excellence through scientific discovery, clinical practice, and health promotion.</p>
  </section>
  <section class="pillar vision">
    <div class="pillar-badge"><span class="fill">VISION</span></div>
    <p class="pillar-text">WSUH Kinesiology graduates are leaders who excel in careers that enhance the quality of life of individuals and communities.</p>
  </section>
  <section class="pillar values">
    <div class="pillar-badge"><span class="fill">VALUES</span></div>
    <p class="pillar-text">Student Success, Science, and Service</p>
  </section>

  <h2 class="competency-heading">Our Graduates Will Be Competent In :</h2>

  <section class="domain science">
    <span class="domain-label">THE SCIENCE OF KINESIOLOGY</span>
    <ul class="domain-list">
      <li>Foundational Concepts of Kinesiology</li>
      <li>Clinical Application</li>
      <li>Scientific Communication</li>
    </ul>
  </section>
  <section class="domain thinking">
    <span class="domain-label">THINKING AND REASONING</span>
    <ul class="domain-list">
      <li>Critical Thinking</li>
      <li>Quantitative Reasoning</li>
      <li>Scientific Inquiry</li>
      <li>Concept Integration</li>
    </ul>
  </section>
  <section class="domain relationships">
    <span class="domain-label">RELATIONSHIPS AND COMMUNICATION</span>
    <ul class="domain-list">
      <li>Cultural Competence</li>
      <li>Professionalism</li>
      <li>Leadership and Teamwork</li>
      <li>Service Orientation/Citizenship</li>
    </ul>
  </section>
  <section class="domain growth">
    <span class="domain-label">INTRAPERSONAL GROWTH</span>
    <ul class="domain-list">
      <li>Cultural Humility/Sensitivity</li>
      <li>Integrity</li>
      <li>Self-Directed</li>
      <li>Dependability</li>
      <li>Mission Oriented</li>
    </ul>
  </section>
</body>
</html>
```